Electrician Letterhead Design MVR

We need some letterhead for our bills and other papers.
Customer address is on the right side (Swiss format)
A4 format

Design should also be applicable on Cards

Target Market(s)

Private Customers, Small Business

Industry/Entity Type

Electrician

Other font styles liked:
• incised 901

Colors
00AB8E
00BBA5
67D7C9
C6EFE9
E9F9F6

```html
<!DOCTYPE html>
<html lang="de">
<head>
<meta charset="utf-8">
<title>MVR Letterhead</title>
<link href="https://fonts.googleapis.com/css2?family=Michroma&family=Open+Sans:wght@400;600&display=swap" rel="stylesheet">
<style>
  :root {
    --teal-deep: #00AB8E;
    --teal: #00BBA5;
    --teal-soft: #67D7C9;
    --teal-pale: #C6EFE9;
    --teal-mist: #E9F9F6;
    --ink: #4a4f52;
    --paper: #ffffff;
    --backdrop: #e4e5e6;
  }
  html, body {
    margin: 0;
    width: 1200px;
    height: 800px;
    overflow: hidden;
    background: var(--backdrop);
  }
  .canvas {
    position: relative;
    width: 1200px;
    height: 800px;
  }
  .letterhead {
    position: absolute;
    left: 331px;
    top: 18px;
    width: 538px;
    height: 764px;
    background: var(--paper);
    box-shadow: 0 4px 18px rgba(0,0,0,0.12);
    overflow: hidden;
  }
  .brand {
    position: absolute;
    left: 44px;
    top: 92px;
    display: flex;
    flex-direction: column;
    gap: 6px;
  }
  .brand-name {
    font-family: "Michroma", sans-serif;
    font-size: 40px;
    line-height: 1;
    color: var(--teal-deep);
    letter-spacing: 1px;
  }
  .brand-line {
    font-family: "Michroma", sans-serif;
    font-size: 7.5px;
    color: var(--teal-deep);
    letter-spacing: 0.2px;
  }
  .contact {
    position: absolute;
    right: 44px;
    top: 40px;
    font-family: "Open Sans", sans-serif;
    font-size: 8px;
    line-height: 1.45;
    color: var(--ink);
  }
  .contact p { margin: 0; }
  .contact .address { margin-bottom: 3px; }
  .contact-item {
    display: flex;
    align-items: center;
    gap: 5px;
  }
  .contact-icon {
    width: 8px;
    height: 8px;
    flex: none;
  }
  .footer-waves {
    position: absolute;
    left: 0;
    bottom: 0;
    width: 538px;
    height: 200px;
    display: block;
  }
</style>
</head>
<body>
<div class="canvas">
  <section class="letterhead">
    <header class="brand">
      <div class="brand-name">MVR</div>
      <div class="brand-line">Elektrotechnik Vanrell GmbH</div>
    </header>

    <address class="contact">
      <p class="address">Lindenweg 14,<br>8000 Musterstadt, Schweiz</p>
      <p class="contact-item">
        <svg class="contact-icon" viewBox="0 0 10 10" aria-hidden="true"><circle cx="5" cy="5" r="5" fill="var(--teal-deep)"/><path d="M3.3 2.6l1 .9-.5.8a3.5 3.5 0 0 0 1.9 1.9l.8-.5.9 1-.8.7A4.6 4.6 0 0 1 2.6 3.4z" fill="#fff"/></svg>
        +41 44 000 12 34
      </p>
      <p class="contact-item">
        <svg class="contact-icon" viewBox="0 0 10 10" aria-hidden="true"><circle cx="5" cy="5" r="5" fill="var(--teal-deep)"/><rect x="3.3" y="2.2" width="3.4" height="5.6" rx="0.6" fill="#fff"/></svg>
        +41 44 000 12 35
      </p>
      <p class="contact-item">
        <svg class="contact-icon" viewBox="0 0 10 10" aria-hidden="true"><circle cx="5" cy="5" r="5" fill="var(--teal-deep)"/><rect x="2.4" y="3.2" width="5.2" height="3.6" fill="#fff"/><path d="M2.4 3.2L5 5.3l2.6-2.1" stroke="var(--teal-deep)" stroke-width="0.6" fill="none"/></svg>
        info@vanrell-elektro.ch
      </p>
      <p class="contact-item">
        <svg class="contact-icon" viewBox="0 0 10 10" aria-hidden="true"><circle cx="5" cy="5" r="5" fill="var(--teal-deep)"/><circle cx="5" cy="5" r="2.6" stroke="#fff" stroke-width="0.7" fill="none"/><path d="M2.4 5h5.2M5 2.4v5.2" stroke="#fff" stroke-width="0.6"/></svg>
        www.vanrell-elektro.ch
      </p>
    </address>

    <svg class="footer-waves" viewBox="0 0 538 200" preserveAspectRatio="none" aria-hidden="true">
      <path d="M0 150 C120 150 200 120 300 80 C390 45 470 20 538 10 L538 200 L0 200 Z" fill="var(--teal-soft)" opacity="0.55"/>
      <path d="M0 160 C130 160 220 130 320 92 C410 58 480 40 538 34 L538 200 L0 200 Z" fill="var(--teal)"/>
      <path d="M0 172 C150 172 240 140 340 105 C420 78 485 64 538 60" stroke="#fff" stroke-width="2" fill="none"/>
      <path d="M0 182 C160 182 260 150 360 118 C440 92 495 82 538 80 L538 200 L0 200 Z" fill="var(--teal-deep)"/>
      <path d="M20 160 C150 150 240 118 330 84 C410 54 480 32 538 24" stroke="#fff" stroke-width="1.2" fill="none" opacity="0.8"/>
    </svg>
  </section>
</div>
</body>
</html>
```